Modern Medical Optometry Website

We need mordern, Patient friendly website. Easy to navigate and enhance our advance medical technology and excellent patient care.
1. HOME PAGE
2. OUR TEAM PAGE
3. EYECARE PAGE - VISION SERVICES, EYE EXAMS, KERATOCONUS CENTER, GLAUCOMA , DIABITES, MELORIDEX EXAM, DIGITAL RETINAL, OCT.
4. MYOPIA CONTROL CLINIC
5. DRY EYE CLINIC
6. EYEWEAR
7. PATIENT CENTER - BLOG
7. CONTACT US
This is our current website www.brivaloka.com
and We want to add more content and a cleaner design like these website
http://tarnwickfolvendale.com/
https://www.qmvorlu.com/

```html
<!DOCTYPE html>
<html lang="en">
<head>
<meta charset="utf-8">
<title>Lumora Optometry</title>
<link href="https://fonts.googleapis.com/css2?family=Montserrat:wght@300;400;500;600&family=Lato:ital,wght@0,400;1,400&display=swap" rel="stylesheet">
<style>
:root{
  --yellow:#f2c31c;
  --band:#ecd02e;
  --teal:#17809c;
  --ink:#2a2a2a;
  --muted:#666;
  --line:#d9d9d9;
  --panel:#f3f3f3;
  --footer:#2c2c2c;
  --white:#fff;
}
*{box-sizing:border-box;margin:0;padding:0}
html,body{width:1200px;height:4100px;overflow:hidden}
body{position:relative;font-family:"Montserrat",sans-serif;color:var(--ink);background:var(--white)}
.abs{position:absolute}

/* hero */
.hero{left:0;top:0;width:1200px;height:692px;background:linear-gradient(100deg,#eef1f2 0%,#dfe5e8 35%,#b7a68d 60%,#6b5a48 80%,#3e352d 100%)}
.brand{left:109px;top:110px;display:flex;align-items:center;gap:12px}
.brand-mark{width:26px;height:26px;background:var(--yellow)}
.brand-name{font-size:26px;font-weight:400;color:var(--yellow);letter-spacing:1px}
.nav{left:250px;top:70px;display:flex;gap:24px;font-size:15px;color:#333}
.nav .active{color:var(--yellow)}
.nav-search{left:1074px;top:72px}
.topline{left:836px;top:28px;font-size:15px;color:#333;display:flex;align-items:center;gap:8px}
.hero-title{left:109px;top:262px;font-size:68px;font-weight:300;line-height:1.12;color:#222;letter-spacing:1px}
.hero-sub{left:109px;top:440px;font-size:20px;color:#333}
.btn-yellow{background:var(--yellow);color:var(--white);font-weight:500;display:flex;align-items:center;justify-content:center}
.hero-btn{left:109px;top:508px;width:235px;height:55px;font-size:15px;letter-spacing:.5px}
.arrow{top:330px}

/* promise */
.promise-title{left:112px;top:810px;font-size:54px;font-weight:300;line-height:1.25;letter-spacing:1px}
.promise-box{left:519px;top:692px;width:681px;height:374px;background:var(--teal);color:var(--white)}
.promise-text{left:63px;top:50px;width:510px;font-size:14px;line-height:2.05}
.btn-outline{left:63px;top:262px;width:134px;height:46px;border:1.5px solid var(--white);font-size:14px;display:flex;align-items:center;justify-content:center;font-weight:500}

/* section titles */
.section-title{left:0;width:1200px;text-align:center;font-size:52px;font-weight:300;letter-spacing:2px}

/* tiles */
.tile{display:flex;align-items:flex-end;justify-content:center;padding-bottom:22px;color:var(--white);font-size:23px;letter-spacing:1px;text-shadow:0 1px 3px rgba(0,0,0,.4)}

/* testimonials */
.quote{width:465px;height:147px;border:1.5px solid #bdbdbd;border-radius:10px;padding:26px 32px;font-family:"Lato",sans-serif;font-style:italic;font-size:17px;line-height:1.7;color:#555}
.tail{width:0;height:0}
.person{font-size:19px;font-weight:500}
.role{font-size:14px;color:var(--muted)}

/* gallery */
.gallery{left:0;top:2375px;width:1200px;height:547px;background:var(--band)}
.gallery-title{left:0;top:90px;width:1200px;text-align:center;font-size:52px;font-weight:300;color:var(--white);letter-spacing:2px}
.g-img{top:194px;width:312px;height:254px}

/* contact */
.map{left:0;top:3567px;width:1200px;height:440px;background:linear-gradient(135deg,#eeeae2,#e4e0d6 50%,#ecebe6)}
.card{left:112px;top:3184px;width:976px;height:443px;background:var(--white);box-shadow:0 2px 12px rgba(0,0,0,.15)}
.card-panel{left:0;top:0;width:334px;height:443px;background:var(--panel)}
.card-heading{left:44px;top:60px;font-size:27px;font-weight:400}
.info{left:44px;display:flex;align-items:center;gap:28px;font-size:14px;color:#444;line-height:1.6}
.info-icon{width:32px;height:32px;border-radius:50%;background:var(--white);display:flex;align-items:center;justify-content:center;flex:none}
.field{left:396px;width:533px;border-bottom:1px solid var(--line);font-size:14px;color:#444;padding-bottom:14px}
.submit{left:396px;top:331px;width:132px;height:52px;border-radius:26px;font-size:15px;letter-spacing:.5px}

/* footer */
.footer{left:0;top:4007px;width:1200px;height:93px;background:var(--footer);color:#ddd}
.copy{left:112px;top:38px;font-size:14px}
.social{top:30px;width:36px;height:36px;border-radius:50%;border:1.5px solid #aaa}
</style>
</head>
<body>

<header>
  <div class="abs hero" role="img" aria-label="Smiling couple wearing sunglasses outdoors"></div>
  <div class="abs topline">
    <svg width="14" height="14" viewBox="0 0 24 24"><path d="M6.6 10.8a15 15 0 0 0 6.6 6.6l2.2-2.2a1 1 0 0 1 1-.25 11.4 11.4 0 0 0 3.6.57 1 1 0 0 1 1 1V20a1 1 0 0 1-1 1A17 17 0 0 1 3 4a1 1 0 0 1 1-1h3.5a1 1 0 0 1 1 1c0 1.25.2 2.45.57 3.57a1 1 0 0 1-.25 1z" fill="#f2c31c"/></svg>
    Call Or Text Us &nbsp;555-204-3170
  </div>
  <div class="abs brand"><span class="brand-mark"></span><span class="brand-name">LUMORA</span></div>
  <nav class="abs nav">
    <span class="active">Home</span><span>Our Team</span><span>Eyecare</span><span>Myopia Control Clinic</span><span>Dry Eye Clinic</span><span>Eyewear</span><span>Blog</span><span>Contact Us</span>
  </nav>
  <svg class="abs nav-search" width="16" height="16" viewBox="0 0 24 24"><circle cx="10" cy="10" r="7" fill="none" stroke="#333" stroke-width="3"/><path d="M15 15l7 7" stroke="#333" stroke-width="3"/></svg>
  <h1 class="abs hero-title">LUMORA<br>OPTOMETRY</h1>
  <p class="abs hero-sub">Vision and eye health are our sole priority.</p>
  <div class="abs btn-yellow hero-btn">MAKE AN APPOINTMENT</div>
  <svg class="abs arrow" style="left:36px" width="22" height="36" viewBox="0 0 22 36"><path d="M18 3L4 18l14 15" fill="none" stroke="#555" stroke-width="3"/></svg>
  <svg class="abs arrow" style="left:1140px" width="22" height="36" viewBox="0 0 22 36"><path d="M4 3l14 15L4 33" fill="none" stroke="#fff" stroke-width="3"/></svg>
</header>

<section>
  <h2 class="abs promise-title">THE LUMORA<br>PROMISE</h2>
  <div class="abs promise-box">
    <p class="abs promise-text">Welcome to Lumora Optometry, where your vision and eye health are our sole priority. We take great pride in providing you with state-of-the-art eyecare matched with personal attention from our staff and doctors. Your quality of life is our goal and we believe that healthy eyesight is vital to achieving it. Our professional and personable staff is highly trained in helping you achieve and maintain healthy eyesight.</p>
    <div class="abs btn-outline">READ MORE</div>
  </div>
</section>

<section>
  <h2 class="abs section-title" style="top:1170px">EYECARE</h2>
  <div class="abs tile" style="left:18px;top:1293px;width:242px;height:235px;background:linear-gradient(135deg,#c98b3a,#7a4a1c)" role="img" aria-label="Close-up of an eye">VISION</div>
  <div class="abs tile" style="left:276px;top:1293px;width:391px;height:235px;background:linear-gradient(135deg,#bdbdbd,#8c8c8c)" role="img" aria-label="Woman in glasses beside an eye chart">EYE EXAMS</div>
  <div class="abs tile" style="left:686px;top:1293px;width:238px;height:235px;background:linear-gradient(180deg,#e0a35c,#7b4a23)" role="img" aria-label="Hands holding glasses at sunset">GLAUCOMA</div>
  <div class="abs tile" style="left:943px;top:1293px;width:238px;height:235px;background:linear-gradient(135deg,#c9a27a,#6b4e33)" role="img" aria-label="Close-up of an eye with lashes">DIABITES</div>
  <div class="abs tile" style="left:18px;top:1547px;width:242px;height:235px;background:linear-gradient(135deg,#a8adb2,#55595e)" role="img" aria-label="Phoropter exam instrument">OCT</div>
  <div class="abs tile" style="left:276px;top:1547px;width:238px;height:235px;background:linear-gradient(135deg,#1c5f8a,#8a3a24)" role="img" aria-label="Digital scan of an iris">DIGITAL RETINAL</div>
  <div class="abs tile" style="left:533px;top:1547px;width:391px;height:235px;background:linear-gradient(135deg,#8a6d5a,#c9b8ab)" role="img" aria-label="Woman adjusting her glasses">KERATOCONUS CENTER</div>
  <div class="abs tile" style="left:943px;top:1547px;width:238px;height:235px;background:linear-gradient(135deg,#e8e8e8,#a8a8a8)" role="img" aria-label="Glasses on a reading chart">MELORIDEX EXAM</div>
</section>

<section>
  <h2 class="abs section-title" style="top:1888px">TESTIMONIALS</h2>
  <div class="abs quote" style="left:112px;top:1998px">"Nam libero tempore, cum soluta nobis est eligendiop tio cumque nihil impedit quo minus id quod maxime placeat facere possimus, omnis. "</div>
  <svg class="abs" style="left:196px;top:2143px" width="60" height="40" viewBox="0 0 60 40"><path d="M10 0L0 38L58 0" fill="#fff" stroke="#bdbdbd" stroke-width="1.5"/><path d="M11 -1h46" stroke="#fff" stroke-width="3"/></svg>
  <div class="abs person" style="left:112px;top:2208px">Owen Hartley</div>
  <div class="abs role" style="left:112px;top:2236px">Nam libero tempore um</div>

  <div class="abs quote" style="left:620px;top:1998px">"Nam libero tempore, cum soluta nobis est eligendiop tio cumque nihil impedit quo minus id quod maxime placeat facere possimus, omnis. "</div>
  <svg class="abs" style="left:704px;top:2143px" width="60" height="40" viewBox="0 0 60 40"><path d="M10 0L0 38L58 0" fill="#fff" stroke="#bdbdbd" stroke-width="1.5"/><path d="M11 -1h46" stroke="#fff" stroke-width="3"/></svg>
  <div class="abs person" style="left:620px;top:2208px">Mira</div>
  <div class="abs role" style="left:620px;top:2236px">Nam libero tempore um</div>
</section>

<section class="abs gallery">
  <h2 class="abs gallery-title">GALLERY</h2>
  <div class="abs g-img" style="left:112px;background:linear-gradient(135deg,#8a6a55,#2e3a4c)" role="img" aria-label="Couple in glasses laughing together"></div>
  <div class="abs g-img" style="left:443px;background:linear-gradient(135deg,#d2d2d2,#9c9c9c)" role="img" aria-label="Hands holding a pair of glasses"></div>
  <div class="abs g-img" style="left:773px;background:linear-gradient(135deg,#b8a68f,#e4dccf)" role="img" aria-label="Woman in glasses using a laptop"></div>
  <svg class="abs" style="left:44px;top:302px" width="20" height="32" viewBox="0 0 20 32"><path d="M16 3L4 16l12 13" fill="none" stroke="#fff" stroke-width="3"/></svg>
  <svg class="abs" style="left:1136px;top:302px" width="20" height="32" viewBox="0 0 20 32"><path d="M4 3l12 13L4 29" fill="none" stroke="#fff" stroke-width="3"/></svg>
</section>

<section>
  <h2 class="abs section-title" style="top:3060px">CONTACT US</h2>
  <div class="abs map" role="img" aria-label="Street map showing the clinic location"></div>
  <div class="abs card">
    <div class="abs card-panel"></div>
    <h3 class="abs card-heading">Contact Information</h3>
    <div class="abs info" style="top:126px">
      <span class="info-icon"><svg width="14" height="16" viewBox="0 0 24 28"><path d="M12 1a9 9 0 0 0-9 9c0 7 9 17 9 17s9-10 9-17a9 9 0 0 0-9-9z" fill="#17809c"/><circle cx="12" cy="10" r="3.5" fill="#fff"/></svg></span>
      <span>4120 Marlow Ave.,<br>Fenbrook, CA 90412</span>
    </div>
    <div class="abs info" style="top:200px">
      <span class="info-icon"><svg width="14" height="14" viewBox="0 0 24 24"><path d="M6.6 10.8a15 15 0 0 0 6.6 6.6l2.2-2.2a1 1 0 0 1 1-.25 11.4 11.4 0 0 0 3.6.57 1 1 0 0 1 1 1V20a1 1 0 0 1-1 1A17 17 0 0 1 3 4a1 1 0 0 1 1-1h3.5a1 1 0 0 1 1 1c0 1.25.2 2.45.57 3.57a1 1 0 0 1-.25 1z" fill="#17809c"/></svg></span>
      <span>555-204-3170</span>
    </div>
    <div class="abs info" style="top:260px">
      <span class="info-icon"><svg width="14" height="14" viewBox="0 0 24 24"><rect x="3" y="8" width="18" height="12" rx="2" fill="#17809c"/><rect x="7" y="3" width="10" height="6" fill="#17809c"/><rect x="7" y="12" width="10" height="2" fill="#fff"/></svg></span>
      <span>555-204-3180</span>
    </div>
    <div class="abs info" style="top:320px">
      <span class="info-icon"><svg width="14" height="12" viewBox="0 0 24 18"><rect x="1" y="1" width="22" height="16" rx="2" fill="#17809c"/><path d="M2 2l10 8 10-8" fill="none" stroke="#fff" stroke-width="2"/></svg></span>
      <span>info@brivaloka.com</span>
    </div>
    <div class="abs field" style="top:58px">Your Name</div>
    <div class="abs field" style="top:118px">Email Address</div>
    <div class="abs field" style="top:178px">Phone Number</div>
    <div class="abs field" style="top:236px;padding-bottom:40px">Message</div>
    <div class="abs btn-yellow submit">SUBMIT</div>
  </div>
</section>

<footer class="abs footer">
  <p class="abs copy">Copyright © 2019, Lumora Optometry . All rights reserved.</p>
  <span class="abs social" style="left:914px"></span>
  <span class="abs social" style="left:958px"></span>
  <span class="abs social" style="left:1002px"></span>
  <span class="abs social" style="left:1046px"></span>
</footer>

</body>
</html>
```